Brightmill Data Works

Our company is about IT hardwares and IT solutions. IT hardware such as PC, RAMS, storage and servers. IT solutions such as project management, BA. We are also selling new technology too.

Target Market(s)

Consumer, Small to Medium Business, Corporate

Requirements
Must have
• The business card must have the following:
• Name:
• Title:
• Contact Number:
• Email address:
• Website:
• Color: Must match the logo color upgrade

```html
<!DOCTYPE html>
<html lang="en">
<head>
<meta charset="utf-8">
<title>Brightmill Data Works – Business Card</title>
<link href="https://fonts.googleapis.com/css2?family=Saira+Semi+Condensed:wght@400;500;700&display=swap" rel="stylesheet">
<style>
  :root{
    --bg:#2a2a2a;
    --orange:#e2862b;
    --orange-deep:#c85d1a;
    --charcoal:#444444;
    --ink:#3b3b3b;
    --paper:#f4f4f4;
    --white:#ffffff;
    --rule:#8a8a8a;
  }
  *{margin:0;padding:0;box-sizing:border-box}
  html,body{width:1200px;height:923px;overflow:hidden}
  body{
    background:var(--bg);
    font-family:"Saira Semi Condensed",sans-serif;
    position:relative;
  }
  .card{
    position:absolute;left:250px;width:700px;height:400px;
    overflow:hidden;border-radius:4px;
  }
  .card-back{
    top:40px;
    background:linear-gradient(135deg,var(--orange) 0%,var(--orange-deep) 100%);
    display:flex;align-items:center;justify-content:center;gap:16px;
  }
  .card-back .brand-mark{width:26px;height:26px;background:var(--white);flex:none}
  .card-back .brand-name{
    color:var(--white);font-weight:700;font-size:40px;letter-spacing:1px;white-space:nowrap;
  }
  .card-front{top:483px;background:var(--paper)}
  .card-front .wave{position:absolute;inset:0;width:100%;height:100%}
  .wave .band{fill:var(--orange)}
  .wave .dark{fill:var(--charcoal)}
  .front-brand{
    position:absolute;left:44px;top:96px;
    display:flex;align-items:flex-start;gap:12px;
  }
  .front-brand .brand-mark{width:18px;height:18px;background:var(--orange);margin-top:7px;flex:none}
  .front-brand .brand-name{
    color:var(--ink);font-weight:700;font-size:30px;line-height:1.05;letter-spacing:.5px;
  }
  .person{position:absolute;left:70px;top:300px;text-align:right;width:200px}
  .person-name{color:var(--white);font-size:26px;font-weight:500;line-height:1}
  .person-title{color:var(--orange);font-size:17px;font-weight:500;letter-spacing:.5px}
  .divider{
    position:absolute;left:300px;top:260px;width:1px;height:110px;background:var(--rule);
  }
  .contacts{
    position:absolute;left:330px;top:262px;list-style:none;
    display:flex;flex-direction:column;gap:12px;
  }
  .contacts li{display:flex;align-items:center;gap:12px;color:var(--white);font-size:18px}
  .contacts .icon{
    width:22px;height:22px;background:var(--orange);border-radius:2px;
    display:flex;align-items:center;justify-content:center;
  }
  .contacts .icon svg{width:14px;height:14px}
</style>
</head>
<body>
  <section class="card card-back" aria-label="Card back">
    <span class="brand-mark"></span>
    <span class="brand-name">BRIGHTMILL DATA WORKS</span>
  </section>

  <section class="card card-front" aria-label="Card front">
    <svg class="wave" viewBox="0 0 700 400" preserveAspectRatio="none" aria-hidden="true">
      <path class="band" d="M0,238 C170,238 280,200 360,140 C440,80 540,52 700,52 L700,400 L0,400 Z"/>
      <path class="dark" d="M0,262 C190,262 300,225 380,165 C460,105 560,78 700,78 L700,400 L0,400 Z"/>
    </svg>

    <div class="front-brand">
      <span class="brand-mark"></span>
      <span class="brand-name">BRIGHTMILL<br>DATA WORKS</span>
    </div>

    <div class="person">
      <p class="person-name">DANA MARLOW</p>
      <p class="person-title">MANAGER</p>
    </div>

    <span class="divider"></span>

    <ul class="contacts">
      <li>
        <span class="icon"><svg viewBox="0 0 16 16"><path fill="#444" d="M4 1l3 3-1.6 1.8a9 9 0 0 0 4.8 4.8L12 9l3 3-2 2.5C7.5 14 2 8.5 1.5 3z"/></svg></span>
        +1-555-014-2287
      </li>
      <li>
        <span class="icon"><svg viewBox="0 0 16 16"><rect x="1.5" y="3.5" width="13" height="9" fill="none" stroke="#444" stroke-width="1.5"/><path d="M1.5 3.5L8 9l6.5-5.5" fill="none" stroke="#444" stroke-width="1.5"/></svg></span>
        dana@brightmilldata.com
      </li>
      <li>
        <span class="icon"><svg viewBox="0 0 16 16" fill="none" stroke="#444" stroke-width="1.3"><circle cx="8" cy="8" r="6.3"/><ellipse cx="8" cy="8" rx="2.8" ry="6.3"/><path d="M1.7 8h12.6M3 4.5h10M3 11.5h10"/></svg></span>
        www.brightmilldata.com
      </li>
    </ul>
  </section>
</body>
</html>
```